Before the kettle boils, pocast with content in its majority of technology

Page dedicated to a pocast with content in its majority of technology. The page also contains the chapters of the podcast (pluggin vocalink) will also contain news. Preferably Worpress. There is already a very basic page with a simple theme, the logo and little more, I would like something more professional. Www.lamparadebolsillo.com The logo does not want to change.

Target Market(s)

Anyone

Colors

Designer to choose colors to be used in the design.

Requirements
Must have
• You can put the vocalink pluggin with the podcast chapters

```html
<!DOCTYPE html>
<html lang="es">
<head>
<meta charset="utf-8">
<title>Before the kettle boils — Podcast</title>
<link rel="stylesheet" href="https://fonts.googleapis.com/css2?family=Roboto:wght@400;500;700&family=Roboto+Condensed:wght@700&display=swap">
<style>
:root{
  --page:#1b1b1b;
  --head:#202020;
  --orange:#f07a1a;
  --orange-dark:#d9650c;
  --card:#ffffff;
  --strip:#f4f4f4;
  --line:#e3e3e3;
  --text:#555555;
  --muted:#8a8a8a;
  --title:#222222;
  --green:#25b37c;
  --play:#f5b915;
  --wave:#c9c9c9;
}
*{box-sizing:border-box;margin:0;padding:0}
html,body{width:1200px;height:4215px;overflow:hidden}
body{background:var(--page);font-family:"Roboto",Arial,sans-serif;color:var(--text);position:relative}
a{color:inherit;text-decoration:none}

.site-header{position:absolute;left:0;top:0;width:1200px;height:170px;
  background:linear-gradient(90deg,#1d1d1d 0%,#2c2c2c 45%,#1d1d1d 100%)}
.header-photo{position:absolute;left:300px;top:0;width:600px;height:170px;
  background:radial-gradient(ellipse at 50% 40%,#3a3a3a 0%,rgba(40,40,40,0) 70%)}
.brand{position:absolute;left:140px;top:40px;display:flex;align-items:center;gap:14px}
.brand-dot{width:64px;height:64px;border-radius:50%;background:var(--orange)}
.brand-name{font-family:"Roboto Condensed",Arial,sans-serif;font-weight:700;font-size:24px;color:var(--orange);text-transform:uppercase;line-height:1.1;width:190px}
.header-social{position:absolute;left:955px;top:20px;display:flex;gap:8px}
.header-social span{width:36px;height:36px;border:2px solid #fff;border-radius:50%}
.header-actions{position:absolute;left:890px;top:80px;display:flex;gap:12px}
.btn{height:34px;padding:0 20px;font-size:12px;font-weight:700;letter-spacing:.5px;color:#fff;display:flex;align-items:center;border-radius:2px}
.btn-ghost{background:#121212}
.btn-orange{background:var(--orange);padding:0 28px}

.post{position:absolute;left:112px;width:731px;background:var(--card);border-radius:3px}
.post-head{height:75px;background:var(--strip);border-bottom:1px solid var(--line);position:relative;padding:18px 0 0 95px}
.post-title{font-size:20px;font-weight:700;color:var(--title)}
.post-author{font-size:11px;font-weight:700;color:var(--orange);margin-top:6px;text-transform:uppercase}
.date-badge{position:absolute;left:-19px;top:18px;width:98px;height:62px;background:var(--orange);color:#fff;display:flex;align-items:center;padding-left:10px;gap:5px}
.date-badge::after{content:"";position:absolute;left:0;bottom:-10px;border-top:10px solid var(--orange-dark);border-left:19px solid transparent}
.date-day{font-size:32px;font-weight:700}
.date-mon{font-size:11px;font-weight:700;line-height:1.2;text-transform:uppercase}
.comment-count{position:absolute;right:22px;top:12px;width:52px;height:52px;border-radius:50%;border:3px solid #ddd;background:#fff;font-size:12px;color:var(--orange);display:flex;align-items:center;justify-content:center}
.post-body{padding:30px 28px 0 28px;font-size:14px;line-height:1.55}
.post-body p{margin-bottom:14px}
.post-foot{position:absolute;left:28px;right:28px;bottom:0;height:64px;border-top:1px solid var(--line);display:flex;align-items:center;justify-content:space-between;font-size:11px;color:var(--muted)}
.share{display:flex;align-items:center;gap:10px;font-weight:700;color:#444;font-size:11px}
.share-icon{width:26px;height:26px;border-radius:50%;border:1px solid #bbb}
.share-dots{display:flex;gap:6px}
.share-dots span{width:22px;height:22px;border-radius:50%}

.pricing{display:flex;gap:14px;background:#f6f6f6;border:1px solid #ddd;padding:14px;margin:10px 0 22px}
.plan{flex:1;background:#fff;border:1px solid #e2e2e2;text-align:center;height:196px;position:relative}
.plan-top{display:flex;align-items:center;justify-content:center;gap:8px;padding-top:14px;color:#4aa;font-size:34px}
.plan-top small{font-size:10px;color:#777}
.plan-price{font-size:26px;color:#555;margin-top:16px}
.plan-old{font-size:12px;color:#999;text-decoration:line-through;margin-left:4px}
.plan-bar{position:absolute;left:0;right:0;bottom:36px;height:22px;background:var(--green);color:#fff;font-size:10px;font-weight:700;line-height:22px}
.plan-radio{position:absolute;left:50%;bottom:9px;width:16px;height:16px;margin-left:-8px;border:1px solid #aaa;border-radius:50%}

.player{height:216px;border:1px solid #e2e2e2;display:flex;margin:22px 0}
.player-main{flex:1;position:relative}
.play-btn{position:absolute;left:18px;top:20px;width:72px;height:72px;border-radius:50%;background:var(--play)}
.play-btn::after{content:"";position:absolute;left:28px;top:22px;border-left:22px solid #fff;border-top:14px solid transparent;border-bottom:14px solid transparent}
.player-title{position:absolute;left:104px;top:24px;width:230px;font-size:19px;color:#333;line-height:1.3}
.player-stats{position:absolute;left:104px;font-size:12px;color:#333}
.player-label{position:absolute;right:20px;top:22px;font-size:13px;font-weight:700;color:#333}
.player-label span{color:var(--play)}
.player-time{position:absolute;left:18px;top:106px;right:20px;display:flex;justify-content:space-between;font-size:11px;color:#666}
.wave{position:absolute;left:18px;right:20px;bottom:10px;height:70px}
.player-art{width:215px;height:100%}

.search{position:absolute;left:866px;top:191px;width:219px;height:56px;background:#fff;border-radius:3px;padding:10px}
.search span{display:block;height:36px;border:1px solid #ddd;font-size:12px;color:#999;line-height:34px;padding-left:10px}
.widget{position:absolute;left:866px;width:219px;background:#fff;border:4px solid var(--orange);border-radius:3px}
.widget-title{height:54px;background:var(--orange);color:#fff;font-size:16px;font-weight:700;padding:16px 0 0 18px;margin:-4px -4px 10px}
.widget ul{list-style:none;padding:0 18px}
.widget li{font-size:12px;color:#444;border-bottom:1px solid #eee;padding:10px 0;line-height:1.4}
.widget li:last-child{border-bottom:0}
.contact li{display:flex;align-items:center;gap:10px}
.contact li i{width:12px;height:12px;border-radius:50%;background:#777;display:block}
.archive li{padding:7px 0;border-bottom:1px dotted #ddd}
.archive li::before{content:"› ";color:#888}

.pagination{position:absolute;top:3958px;left:112px;width:731px;display:flex;justify-content:center;gap:12px}
.pagination span{height:34px;min-width:34px;padding:0 10px;border-radius:17px;background:#fff;color:#555;font-size:12px;display:flex;align-items:center;justify-content:center}
.pagination .current{background:var(--orange);color:#fff}
.site-footer{position:absolute;top:4080px;left:0;width:1200px;text-align:center;font-size:12px;color:#888}
.footer-social{display:flex;justify-content:center;gap:10px;margin-bottom:14px}
.footer-social span{width:36px;height:36px;border-radius:50%;border:2px solid #fff}
.site-footer p{margin-bottom:6px}
</style>
</head>
<body>

<svg width="0" height="0" style="position:absolute">
  <defs>
    <pattern id="wave-bars" width="5" height="10" patternUnits="userSpaceOnUse"><rect width="3" height="10" fill="#c9c9c9"/></pattern>
    <symbol id="waveform" viewBox="0 0 440 70" preserveAspectRatio="none">
      <path d="M0 70 L0 48 L20 40 L40 30 L60 42 L80 25 L100 38 L120 20 L140 34 L160 28 L180 44 L200 18 L220 36 L240 30 L260 46 L280 26 L300 38 L320 22 L340 40 L360 32 L380 45 L400 28 L420 42 L440 36 L440 70 Z" fill="url(#wave-bars)"/>
    </symbol>
  </defs>
</svg>

<header class="site-header">
  <div class="header-photo" role="img" aria-label="Microphone photo in dark tones behind the header"></div>
  <div class="brand"><span class="brand-dot"></span><span class="brand-name">Before the kettle boils</span></div>
  <div class="header-social"><span></span><span></span><span></span></div>
  <div class="header-actions"><a class="btn btn-ghost">REGISTER</a><a class="btn btn-orange">LOGIN</a></div>
</header>

<article class="post" style="top:191px;height:374px">
  <div class="post-head">
    <div class="date-badge"><span class="date-day">19</span><span class="date-mon">May<br>2017</span></div>
    <h2 class="post-title">Cambio de logo</h2>
    <div class="comment-count">229</div>
  </div>
  <div class="post-body">
    <p>Hola a Tod@s!</p>
    <p>¿Salta a la vista no?, pues sí, renovamos diseño del logo y algo en la web. Aquí los cambios irán poco a poco pero procuraré dejar todo lo que quiero modificar hecho en una semana (como mucho, todo dependerá del tiempo que le pueda dedicar aunque lo difícil ya está hecho.</p>
    <p>Nada más, nos escuchamos en el siguiente!</p>
  </div>
  <div class="post-foot">
    <div class="share-dots"><span style="background:#3b5998"></span><span style="background:#1da1f2"></span><span style="background:#0077b5"></span><span style="background:#dd4b39"></span><span style="background:#999"></span><span style="background:#25d366"></span><span style="background:#e60023"></span><span style="background:#777"></span></div>
    <span>Publicado en Sin categoría | Deja un comentario</span>
  </div>
</article>

<article class="post" style="top:582px;height:1123px">
  <div class="post-head">
    <div class="date-badge"><span class="date-day">17</span><span class="date-mon">May<br>2017</span></div>
    <h2 class="post-title">¿Te gustan las series?¿Conoces cinelingo.tv?</h2>
    <div class="post-author">De Raulix</div>
    <div class="comment-count">229</div>
  </div>
  <div class="post-body">
    <p>Hola a tod@s!</p>
    <p>Hoy capítulo dedicado a los amantes de las series y las películas. Se trata del servicio de vídeo en streaming de la web cinelingo.tv portal dedicado al aprendizaje de inglés mediante el método de ver películas y series en inglés con subtítulos.</p>
    <p>El catálogo es muy amplio, actual y completo. Están prácticamente todas las series de la actualidad al día y los clásicos más famosos. Te puedes registrar desde una cuenta de Buscalo, Caralibro o Chirpa, rápido y sencillo. Hay opciones gratuitas (límite de 60 minutos al día) y de pago, donde se elimina el límite de minutos y permite descargas. Estos son los precios:</p>
    <div class="pricing">
      <div class="plan"><div class="plan-top">1 <small>mes</small></div><div class="plan-price">6 €</div><div class="plan-bar">base</div><span class="plan-radio"></span></div>
      <div class="plan"><div class="plan-top">3 <small>meses</small></div><div class="plan-price">16 €<span class="plan-old">18 €</span></div><div class="plan-bar">descuento de 11%</div><span class="plan-radio"></span></div>
      <div class="plan"><div class="plan-top">6 <small>meses</small></div><div class="plan-price">28 €<span class="plan-old">36 €</span></div><div class="plan-bar">descuento de 22%</div><span class="plan-radio"></span></div>
      <div class="plan"><div class="plan-top">12 <small>meses</small></div><div class="plan-price">48 €<span class="plan-old">72 €</span></div><div class="plan-bar">descuento de 33%</div><span class="plan-radio"></span></div>
    </div>
    <p>Es fácil conseguir descuentos sobre todo en la cuenta anual, actualmente están ofreciendo 2 años por 40€ en lugar de un año. Buscad un poco y veréis.</p>
    <p>En el catálogo entran todas las plataformas actuales, hay series de Flixa, Canal Norte, Tiendazo, etc. En una búsqueda rápida no echarás de menos ninguna serie.</p>
    <p>Por si fuera poca, no tiene aplicación de dispositivo móvil aunque no le haga falta, es html5 y desde cualquier navegador de un dispositivo móvil funciona muy bien y se puede poner a pantalla completa.</p>
    <p>Es gratis probadla y veréis.</p>
    <p>Nos escuchamos en el siguiente.</p>
    <div class="player">
      <div class="player-main">
        <div class="play-btn"></div>
        <div class="player-title">¿Te gustan las series?¿Conoces cinelingo.tv?</div>
        <div class="player-stats" style="top:84px">♥ 1 &nbsp; ➦ &nbsp; ●</div>
        <div class="player-label">Vocalink<span>★</span></div>
        <div class="player-time"><span>00:00</span><span>10:58</span></div>
        <svg class="wave"><use href="#waveform" width="100%" height="100%"/></svg>
      </div>
      <div class="player-art" role="img" aria-label="Episode artwork: collage of series posters" style="background:linear-gradient(135deg,#3a2a22,#6b4a3a 40%,#1f2430)"></div>
    </div>
  </div>
  <div class="post-foot">
    <div class="share"><span class="share-icon"></span>COMPARTE</div>
    <span>Publicado en Sin categoría | Deja un comentario</span>
  </div>
</article>

<article class="post" style="top:1742px;height:618px">
  <div class="post-head">
    <div class="date-badge"><span class="date-day">23</span><span class="date-mon">Nov<br>2016</span></div>
    <h2 class="post-title">Seguridad en tu Mail</h2>
    <div class="post-author">De Raulix</div>
    <div class="comment-count">229</div>
  </div>
  <div class="post-body">
    <p>¡Hola a todos!</p>
    <p>Hoy poco más que decir por aquí de los dicho en el podcast. Para aquellos que necesiten un punto más de seguridad en el correo electrónico está VaultPost. Planes gratuitos y de pago, codificación, mensajes que se pueden auto destruir, etc.</p>
    <p>VaultPost</p>
    <p>Un saludo, nos escuchamos en el siguiente.</p>
    <div class="player">
      <div class="player-main">
        <div class="play-btn"></div>
        <div class="player-title">Seguridad en tu Mail</div>
        <div class="player-stats" style="top:60px">♥ 1 &nbsp; ➦ &nbsp; ●</div>
        <div class="player-label">Vocalink<span>★</span></div>
        <div class="player-time"><span>00:00</span><span>09:53</span></div>
        <svg class="wave"><use href="#waveform" width="100%" height="100%"/></svg>
      </div>
      <div class="player-art" role="img" aria-label="Episode artwork for secure mail" style="background:#6a5ea8"></div>
    </div>
  </div>
  <div class="post-foot">
    <div class="share"><span class="share-icon"></span>COMPARTE</div>
    <span>Publicado en Sin categoría | Deja un comentario</span>
  </div>
</article>

<article class="post" style="top:2390px;height:710px">
  <div class="post-head">
    <div class="date-badge"><span class="date-day">20</span><span class="date-mon">Nov<br>2016</span></div>
    <h2 class="post-title">Kaiyo Tab2, calidad precio insuperable</h2>
    <div class="post-author">De Raulix</div>
    <div class="comment-count">229</div>
  </div>
  <div class="post-body">
    <p>Con un poco de retraso publicamos el post del podcast de la tableta de Kaiyo. Tableta que como viene siendo habitual de la marca, da mucho más de lo que cuesta.</p>
    <p>Os lo comento más detalladamente en el podcast pero es una tableta con un chip Corex Nimbus N5 Z8000, que permite la instalación de SysOne además de Droidal. 2 Gb de RAM, almacenamiento de 16 o 64, 7,9 pulgadas en una fantástica pantalla, que la hacen cumplir más que de sobra en su funcionamiento y a un precio muy apetecible.</p>
    <p>Además como en mi caso, no es raro conseguir un cupón de descuento para poder adquirirla a un mejor precio.</p>
    <p>Si tenéis cualquier duda os lo respondo en los comentarios.</p>
    <p>Un saludo y nos escuchamos en el siguiente</p>
    <div class="player">
      <div class="player-main">
        <div class="play-btn"></div>
        <div class="player-title">Kaiyo Tab2, calidad precio insuperable</div>
        <div class="player-stats" style="top:84px">♥ 2 &nbsp; ➦ &nbsp; ●</div>
        <div class="player-label">Vocalink<span>★</span></div>
        <div class="player-time"><span>00:00</span><span>25:31</span></div>
        <svg class="wave"><use href="#waveform" width="100%" height="100%"/></svg>
      </div>
      <div class="player-art" role="img" aria-label="Episode artwork for the tablet review" style="background:#f26b1d"></div>
    </div>
  </div>
  <div class="post-foot">
    <div class="share"><span class="share-icon"></span>COMPARTE</div>
    <span>Publicado en Sin categoría | Deja un comentario</span>
  </div>
</article>

<article class="post" style="top:3133px;height:773px">
  <div class="post-head">
    <div class="date-badge"><span class="date-day">20</span><span class="date-mon">Jul<br>2016</span></div>
    <h2 class="post-title">Podcast futuros, vocalink, seriere recomendada</h2>
    <div class="post-author">De Raulix</div>
    <div class="comment-count">229</div>
  </div>
  <div class="post-body">
    <p>Podcast de hoy variado, un adelanto de uno o una serie (ya veremos) de podcast que voy a grabar en un futuro, opinión de los nuevos planes de precios de Vocalink y la recomendación de una serie Los Restantes.</p>
    <p>Como ya os comento en el podcast el tema Notaria está ya muy adelantado, solo falta determinar el formato, uno más largo 2 cortos, uno a cada aplicación... Ya veremos.</p>
    <p>Tema Vocalink, hay subida de precios y cambios en las cuentas gratuitas como la mía, menos horas de alojamiento de los podcast, se reducen de la mitad de horas y las cuentas premium aumentan de precio. Yo seguiré igual, cuenta gratuita cuando sea necesario iré borrando podcast, el feed debe de Vocalink y no me apetece de momento estar haciendo cambios. Los podcast también se suben a Ondavox (enlace de Ondavox), así que si necesitáis alguno que se haya borrado de Vocalink, allí los tenéis.</p>
    <p>Los Restantes, primera temporada suuuumm buena, de menos a más, pero la segunda es una maravilla, merece ver la serie para ver esa segunda temporada (y que la primera tampoco está mal). Otra recomendación es su banda sonora.</p>
    <p>Y poco más, nos escuchamos en el siguiente.</p>
    <div class="player">
      <div class="player-main" style="background:#2a2f38">
        <div class="play-btn"></div>
        <div class="player-title" style="color:#fff">Podcast futuros, Vocalink, serie recomendada</div>
        <div class="player-label" style="color:#fff">Vocalink<span>★</span></div>
        <div class="player-time" style="color:#ccc"><span>00:00</span><span>13:20</span></div>
        <svg class="wave"><use href="#waveform" width="100%" height="100%"/></svg>
      </div>
      <div class="player-art" role="img" aria-label="Episode artwork: underwater scene in deep blue" style="background:linear-gradient(180deg,#3f8fb0,#0f3550)"></div>
    </div>
  </div>
  <div class="post-foot">
    <div class="share"><span class="share-icon"></span>COMPARTE</div>
    <span>Publicado en Sin categoría | Deja un comentario</span>
  </div>
</article>

<div class="search"><span>Buscar...</span></div>

<aside class="widget" style="top:295px;height:345px">
  <h3 class="widget-title">Recent Posts</h3>
  <ul>
    <li>Cambio de logo</li>
    <li>¿Te gustan las series?¿Conoces cinelingo.tv?</li>
    <li>Un anuncio y una prueba</li>
    <li>Seguridad en tu Mail</li>
    <li>Kaiyo Tab2, calidad precio insuperable</li>
  </ul>
</aside>

<aside class="widget contact" style="top:648px;height:245px">
  <h3 class="widget-title">Contacto</h3>
  <ul>
    <li><i></i>Chirpa</li>
    <li><i></i>Vocalink</li>
    <li><i></i>Ondavox</li>
    <li><i></i>Mail</li>
  </ul>
</aside>

<aside class="widget archive" style="top:900px;height:766px">
  <h3 class="widget-title">Archives</h3>
  <ul>
    <li>May 2017</li><li>April 2017</li><li>March 2017</li><li>February 2017</li><li>January 2017</li>
    <li>December 2016</li><li>November 2016</li><li>October 2016</li><li>September 2016</li><li>August 2016</li>
    <li>July 2016</li><li>June 2016</li><li>May 2016</li><li>April 2016</li><li>March 2016</li>
    <li>February 2016</li><li>January 2016</li>
  </ul>
</aside>

<nav class="pagination">
  <span>« Prev</span><span class="current">01</span><span>02</span><span>03</span><span>05</span><span>06</span><span>Next »</span>
</nav>

<footer class="site-footer">
  <div class="footer-social"><span></span><span></span><span></span></div>
  <p>Copyright © 2017 Before the kettle boils. All Rights Reserved.</p>
  <p>Terms of Use | Privacy Policy | Sitemap</p>
</footer>

</body>
</html>
```